Stationery Design Project for Mindwell Care Clinic

I would like you to design a letterhead and appt cards and letterhead. i have attached our current brochure so that you can see the kind of clinic that we are - for some context.

Generally our letters will go to General Practitioners.
Appt cards to clients. The text can stay the same as current documents as attached but the design obviously needs to be totally changed.

We are a psychology clinic with several psychologists that work for me. THe psychologists come and go so I am not wanting to list their names on the stationary.

In terms of letterhead my name (dr marion tasker) needs to be on there..eg dr marion tasker & associates.

With envelopes we need to be discrete therefore we simply have MCC & our address.

Everything goes under the banner of Mindwell Care Clinic Pty Ltd.

I would like it to be consistent in theme/colours with the logo you designed and our website which has just gone live www.mindwellcareclinic.com.au

Target Market(s)

General practitioners, potential referrers usually in the medical/health field,

Industry/Entity Type

Clinic

Requirements
Must have
• Logo

Address Suite 4, 2287 Larkmoor Rd, Larkmoor West 3172
P 9362 5184 F 9362 5190 E info@mindwellcareclinic.com.au
W mindwellcareclinic.com.au

Mindwell Care Clinic Pty Ltd (small font)
ABN (ill need to provide this) (small font)
Nice to have
• I really like in my website how the colours are graded in the banners...I think this gives a softer feel...so if something like that would look good in our stationary then please use that kind of technique too...but you guys are the experts.

```html
<!DOCTYPE html>
<html lang="en">
<head>
<meta charset="utf-8">
<title>MCC Envelope</title>
<link rel="stylesheet" href="https://fonts.googleapis.com/css2?family=Lato:wght@400&display=swap">
<style>
  :root {
    --backdrop: #eeefef;
    --paper: #ffffff;
    --ink: #6d6e70;
    --ink-soft: #808184;
    --mark: #d9dadb;
  }
  html, body {
    margin: 0;
    padding: 0;
    width: 1200px;
    height: 900px;
    overflow: hidden;
    background: var(--backdrop);
    font-family: "Lato", sans-serif;
  }
  .envelope {
    position: absolute;
    left: 190px;
    top: 244px;
    width: 820px;
    height: 411px;
    background: var(--paper);
  }
  .sender {
    position: absolute;
    left: 43px;
    top: 47px;
    display: flex;
    align-items: flex-start;
  }
  .sender-dot {
    width: 68px;
    height: 68px;
    display: block;
  }
  .sender-details {
    margin-left: 12px;
    color: var(--ink);
  }
  .sender-name {
    margin: 0;
    font-size: 33px;
    font-weight: 400;
    line-height: 1;
    letter-spacing: 0.5px;
    padding-top: 7px;
  }
  .sender-address {
    margin: 4px 0 0;
    font-size: 11px;
    line-height: 14px;
    color: var(--ink-soft);
    font-style: normal;
  }
</style>
</head>
<body>
  <main class="envelope">
    <div class="sender">
      <svg class="sender-dot" viewBox="0 0 68 68" aria-hidden="true">
        <circle cx="34" cy="34" r="30" fill="var(--mark)"/>
      </svg>
      <div class="sender-details">
        <h1 class="sender-name">MCC</h1>
        <address class="sender-address">Suite 4, 2287 Larkmoor Rd<br>Larkmoor West 3172</address>
      </div>
    </div>
  </main>
</body>
</html>
```